Australian Trucking Company Requires Professional Looking Stationary

We require a professional looking stationary design that incorporates our newly designed logo.

Our business, called "Brell Haulage Contracting", provides contracting work, transport and logistics to business in Western Australia particularly with links to the mining sector.

We are a small business looking to expand and our new logo and our new stationary will help develop our brand image in our market place.

Target Market(s)

Businesses and Corporation with links to the Mining Sector

Industry/Entity Type

Small Business

Requirements
Must have
• The letterhead must have the following details:
The new logo

Text saying: "Brell Holdings Pty Ltd (ACN 582 316 907) ATF The Brell Discretionary Trust T/AS"
"ABN 71 834 209 553"
Address "P.O Box 817 Wattlegrove WA, 6958"
Phone: 08 9352 7140
Email: brellhaul@mailbox-example.com.au

The text on the letterhead should be editable as the details are likely to change in the near future. Provision should be made for a website address all though one isn't available at the moment.

The styling, layout and font text is entirely up to the designer.

```html
<!DOCTYPE html>
<html lang="en">
<head>
<meta charset="utf-8">
<title>Brell Haulage Contracting – Business Card</title>
<link rel="stylesheet" href="https://fonts.googleapis.com/css2?family=Open+Sans:wght@400;600;700;800&display=swap">
<style>
  :root {
    --page-bg: #dcd9d5;
    --card-white: #ffffff;
    --card-silver: #e4e4e4;
    --brand-red: #d3141f;
    --brand-red-dark: #8e0d14;
    --brand-red-light: #ee2a32;
    --ink: #3a3a3a;
    --ink-soft: #555555;
    --rule: #bdbdbd;
    --swoosh-grey: #c9c9c9;
  }
  * { box-sizing: border-box; margin: 0; padding: 0; }
  html, body {
    width: 1200px;
    height: 426px;
    overflow: hidden;
    background: var(--page-bg);
    font-family: "Open Sans", Arial, sans-serif;
    color: var(--ink);
  }
  .canvas { position: relative; width: 1200px; height: 426px; }

  .card {
    position: absolute;
    top: 58px;
    width: 521px;
    height: 296px;
    border-radius: 18px;
    overflow: hidden;
    background: linear-gradient(160deg, var(--card-white) 0%, #f6f6f6 45%, var(--card-silver) 100%);
    box-shadow: 0 6px 14px rgba(0,0,0,0.28);
  }
  .card--front { left: 67px; }
  .card--back { left: 616px; }

  .brand {
    position: absolute;
    left: 32px;
    top: 26px;
    display: flex;
    align-items: flex-start;
    gap: 14px;
  }
  .brand__mark {
    width: 20px;
    height: 20px;
    margin-top: 8px;
    background: var(--brand-red);
  }
  .brand__name {
    color: var(--brand-red);
    font-weight: 800;
    font-size: 27px;
    line-height: 29px;
    text-transform: uppercase;
    letter-spacing: 0.5px;
  }

  .contact {
    position: absolute;
    left: 33px;
    top: 150px;
    font-size: 11px;
    line-height: 17px;
    color: var(--ink);
  }
  .contact__row { display: flex; align-items: center; gap: 5px; white-space: nowrap; }
  .contact__icon { width: 11px; height: 11px; fill: var(--ink-soft); flex: none; }
  .contact__divider {
    position: absolute;
    left: 246px;
    top: 151px;
    width: 1px;
    height: 34px;
    background: var(--rule);
  }
  .address {
    position: absolute;
    left: 254px;
    top: 150px;
    font-size: 11.5px;
    line-height: 17px;
    font-style: normal;
    white-space: nowrap;
  }
  .address__line:first-child { padding-left: 10px; }

  .illustration--truck-small {
    position: absolute;
    left: 392px;
    top: 116px;
    width: 116px;
    height: 88px;
    border-radius: 10px;
    background: linear-gradient(135deg, #6a6a6a 0%, #2a2a2a 100%);
  }
  .illustration--truck-large {
    position: absolute;
    left: 160px;
    top: 35px;
    width: 260px;
    height: 230px;
    border-radius: 16px;
    background: radial-gradient(circle at 40% 40%, var(--brand-red-light) 0%, var(--brand-red) 45%, var(--brand-red-dark) 100%);
  }

  .legal {
    position: absolute;
    left: 30px;
    top: 216px;
    font-size: 11px;
    line-height: 16.5px;
    color: var(--ink);
    white-space: nowrap;
  }
  .legal__abn { margin-top: 4px; }

  .swoosh { position: absolute; left: 0; top: 0; }

  .holder {
    position: absolute;
    left: 300px;
    top: 240px;
    width: 200px;
    text-align: center;
    color: #ffffff;
  }
  .holder__name { font-size: 18px; font-weight: 600; line-height: 22px; }
  .holder__title { font-size: 12px; line-height: 17px; margin-top: 1px; }
</style>
</head>
<body>
<main class="canvas">

  <section class="card card--front" aria-label="Business card front">
    <svg class="swoosh" width="521" height="296" viewBox="0 0 521 296" aria-hidden="true">
      <defs>
        <linearGradient id="swooshRed" x1="0" y1="0" x2="1" y2="0">
          <stop offset="0" stop-color="#b50f18"/>
          <stop offset="0.5" stop-color="#e5222b"/>
          <stop offset="1" stop-color="#9a0c14"/>
        </linearGradient>
      </defs>
      <path d="M0,252 C110,278 230,262 330,228 C420,196 480,190 521,188 L521,198 C480,200 420,208 330,238 C230,272 110,290 0,266 Z" fill="var(--swoosh-grey)"/>
      <path d="M0,266 C110,290 230,272 330,238 C420,208 480,200 521,198 L521,296 L0,296 Z" fill="url(#swooshRed)"/>
    </svg>

    <div class="brand">
      <span class="brand__mark" aria-hidden="true"></span>
      <p class="brand__name">Brell<br>Haulage<br>Contracting</p>
    </div>

    <div class="contact">
      <p class="contact__row">
        <svg class="contact__icon" viewBox="0 0 24 24" aria-hidden="true"><path d="M6.6 10.8c1.4 2.8 3.8 5.1 6.6 6.6l2.2-2.2c.3-.3.7-.4 1-.2 1.1.4 2.3.6 3.6.6.6 0 1 .4 1 1V20c0 .6-.4 1-1 1C10.6 21 3 13.4 3 4c0-.6.4-1 1-1h3.5c.6 0 1 .4 1 1 0 1.3.2 2.5.6 3.6.1.3 0 .7-.2 1z"/></svg>
        08 9352 7140
      </p>
      <p class="contact__row">
        <svg class="contact__icon" viewBox="0 0 24 24" aria-hidden="true"><path d="M2 5h20v14H2z M4 7v.5l8 5 8-5V7z" fill-rule="evenodd"/></svg>
        brellhaul@mailbox-example.com.au
      </p>
    </div>
    <span class="contact__divider" aria-hidden="true"></span>
    <address class="address">
      <p class="address__line">P.O Box 817</p>
      <p class="address__line">Wattlegrove WA, 6958</p>
    </address>

    <div class="illustration--truck-small" role="img" aria-label="Illustration of a black and white prime mover truck in motion"></div>

    <div class="legal">
      <p>Brell Holdings Pty Ltd (ACN 582 316 907) ATF</p>
      <p>The Brell Discretionary Trust T/AS</p>
      <p class="legal__abn">ABN 71 834 209 553</p>
    </div>

    <div class="holder">
      <p class="holder__name">Persons name</p>
      <p class="holder__title">Manager</p>
    </div>
  </section>

  <section class="card card--back" aria-label="Business card back">
    <div class="illustration--truck-large" role="img" aria-label="Large red illustration of a prime mover truck driving forward"></div>
  </section>

</main>
</body>
</html>
```